AGP letterhead

We need a letterhead design for our new company based in Los Angeles called "Amber Gate Pictures". We develop film and television projects. We work with investors, financiers, film production companies, film distribution and sales companies as well as studios. We would like to incorporate our logo (see attached) but make the letterhead simple and elegant. We need to include: logo, company address, phone number and company website.
Updates

Hello designers, Thanks for your submissions. For our letterhead, we are looking for something more simple and elegant. No heavy bars or lines. Make it feel light and clean. Not a lot of ink on the page. Use the logo and contact info but think "clean", "streamlined" and mostly white paper. Looking forward to seeing more... thanks! Amber Gate Pictures team

Target Market(s)

Studio executives, talent agents and agencies, financiers, investors.

Industry/Entity Type

It Company

Requirements
Must have
• Amber Gate Pictures logo (see attached). Logo may be cropped and altered appropriately for elegant letterhead design.
• Please include:
• COMPANY ADDRESS:
• Tolvane Arts Park
• 2850 Delmore Street
• Crest Hall, 2nd Floor
• Larkmoor Bay, CA 90412
• COMPANY WEBSITE:
• www.ambergatepicturesco.example
• COMPANY PHONE NUMBER:
• 555-604-2187

```html
<!DOCTYPE html>
<html lang="en">
<head>
<meta charset="utf-8">
<title>Amber Gate Pictures – Stationery</title>
<link href="https://fonts.googleapis.com/css2?family=Source+Sans+3:wght@400;600;700&display=swap" rel="stylesheet">
<style>
  :root {
    --backdrop: #3c4a4f;
    --backdrop-light: #4a5a60;
    --paper: #ffffff;
    --ink: #1a1a1a;
    --ink-soft: #333333;
    --mark-black: #000000;
    --mark-panel: #0b0d0f;
    --accent-blue: #29a9e0;
    --accent-red: #e0483a;
    --slot-grey: #e9eaeb;
  }
  * { box-sizing: border-box; margin: 0; padding: 0; }
  html, body { width: 1200px; height: 1000px; overflow: hidden; }
  body {
    position: relative;
    font-family: "Source Sans 3", "Helvetica Neue", Arial, sans-serif;
    color: var(--ink);
    background: radial-gradient(ellipse at 50% 45%, var(--backdrop-light) 0%, var(--backdrop) 75%);
  }
  .sheet { position: absolute; background: var(--paper); border-radius: 12px; overflow: hidden; }

  /* Brand lockup */
  .brand-lockup {
    position: absolute; display: flex; flex-direction: column; align-items: center; justify-content: center;
    background: var(--mark-black); gap: 6px; text-align: center;
  }
  .brand-dot { border-radius: 50%; background: var(--accent-blue); }
  .brand-name {
    color: var(--accent-blue); font-weight: 700; text-transform: uppercase;
    letter-spacing: 0.06em; line-height: 1.05;
  }

  /* Business cards */
  .card { top: 86px; height: 118px; }
  .card--front { left: 147px; width: 225px; }
  .card--front .brand-lockup { left: 66px; top: 0; width: 92px; height: 118px; }
  .card--front .brand-dot { width: 30px; height: 30px; }
  .card--front .brand-name { font-size: 7px; }

  .card--contact { left: 419px; width: 224px; }
  .card--contact .brand-lockup { left: 123px; top: 0; width: 70px; height: 118px; }
  .card--contact .brand-dot { width: 20px; height: 20px; }
  .card--contact .brand-name { font-size: 5.5px; }

  .card--round { left: 691px; width: 229px; }
  .card__corner-disc {
    position: absolute; left: 140px; top: 40px; width: 98px; height: 98px; border-radius: 50%;
    background: var(--mark-panel);
  }

  .person { position: absolute; left: 16px; top: 14px; }
  .person__name { font-size: 13px; font-weight: 400; color: var(--ink); line-height: 1; }
  .person__title { font-size: 7px; color: var(--ink-soft); margin-top: 5px; }
  .contact-list { position: absolute; left: 16px; top: 76px; list-style: none; font-size: 8px; line-height: 10.5px; color: var(--ink); }
  .contact-list b { display: inline-block; width: 13px; font-weight: 400; color: var(--accent-blue); }
  .card--contact .contact-list li span { font-weight: 600; }
  .card--round .contact-list b { color: var(--accent-red); }

  /* Letterhead */
  .letterhead { left: 125px; top: 265px; width: 441px; height: 599px; }
  .letterhead .brand-lockup { left: 42px; top: 15px; width: 78px; height: 71px; gap: 5px; }
  .letterhead .brand-dot { width: 24px; height: 24px; }
  .letterhead .brand-name { font-size: 6.5px; }
  .letter__salutation { position: absolute; left: 48px; top: 174px; font-size: 11.5px; }
  .letter__body { position: absolute; left: 48px; top: 210px; width: 328px; font-size: 7.9px; line-height: 11.5px; text-align: justify; }
  .letter__body p + p { margin-top: 11.5px; }
  .letter__signature { position: absolute; left: 48px; top: 424px; }
  .letter__signature .person__name { font-size: 11px; }
  .letter__signature .person__title { font-size: 6px; margin-top: 4px; }
  .letter__footer { position: absolute; right: 65px; top: 550px; text-align: right; font-size: 6px; line-height: 12px; color: var(--ink-soft); white-space: nowrap; }
  .footer__divider { display: inline-block; width: 1px; height: 10px; background: var(--accent-blue); vertical-align: middle; margin: 0 6px 0 8px; }

  /* Presentation folder */
  .folder { left: 635px; top: 265px; width: 441px; height: 599px; }
  .folder__band { position: absolute; left: 191px; top: 0; width: 171px; height: 599px; background: var(--mark-black); }
  .folder .brand-lockup {
    left: 202px; top: 161px; width: 144px; height: 196px; gap: 14px;
    background: linear-gradient(180deg, #101316 0%, #050607 100%);
  }
  .folder .brand-dot { width: 62px; height: 62px; }
  .folder .brand-name { font-size: 12px; }
  .folder__slot {
    position: absolute; left: 410px; top: 130px; width: 40px; height: 195px;
    border-radius: 14px 0 0 14px; background: var(--slot-grey);
  }
</style>
</head>
<body>

  <section class="sheet card card--front" aria-label="Business card front">
    <div class="brand-lockup">
      <span class="brand-dot"></span>
      <span class="brand-name">Amber Gate<br>Pictures</span>
    </div>
  </section>

  <section class="sheet card card--contact" aria-label="Business card back">
    <div class="person">
      <p class="person__name">John Doe</p>
      <p class="person__title">Co-Founder &amp; CEO</p>
    </div>
    <ul class="contact-list">
      <li><b>T:</b><span>(912) 555-1234</span></li>
      <li><b>M:</b><span>john@yourwebsite.com</span></li>
      <li><b>W:</b><span>yourwebsite.com</span></li>
    </ul>
    <div class="brand-lockup">
      <span class="brand-dot"></span>
      <span class="brand-name">Amber Gate<br>Pictures</span>
    </div>
  </section>

  <section class="sheet card card--round" aria-label="Business card alternate">
    <div class="person">
      <p class="person__name">John Doe</p>
      <p class="person__title">Co-Founder &amp; CEO</p>
    </div>
    <ul class="contact-list">
      <li><b>T:</b>(912) 555-1234</li>
      <li><b>M:</b>john@yourwebsite.com</li>
      <li><b>W:</b>yourwebsite.com</li>
    </ul>
    <span class="card__corner-disc"></span>
  </section>

  <section class="sheet letterhead" aria-label="Letterhead">
    <div class="brand-lockup">
      <span class="brand-dot"></span>
      <span class="brand-name">Amber Gate<br>Pictures</span>
    </div>
    <p class="letter__salutation">Dear Mr. Smith,</p>
    <div class="letter__body">
      <p>Lorem ipsum dolor sit amet, consectetur adipiscing elit. Donec orci purus, luctus vitae dignissim eu, iaculis sed purus. Vivamus faucibus, ipsum nec aliquet viverra, leo mauris condimentum ligula, sit amet sagittis enim ligula quis arcu. Nam egestas tortor id nisi porttitor mattis. In tortor ante, ultricies in suscipit a, tempus non massa. Vivamus et auctor mi. Fusce vel massa nulla. Phasellus nec eros mauris, et scelerisque orci. Donec malesuada orci vitae nulla accumsan porta a id massa. Quisque accumsan iaculis magna sit amet fringilla. Maecenas consequat, magna eget tincidunt semper, odio nibh rutrum mi, id feugiat ante nisi eu risus. Vestibulum nunc orci, rhoncus a placerat in, ultricies in mi. Cras mattis varius eros, vel fringilla nisi suscipit eget.</p>
      <p>Quisque scelerisque sagittis nulla at porttitor. Mauris a justo et tellus interdum tristique. Sed id augue vitae urna euismod commodo aliquet a quam. Pellentesque arcu velit, cursus et malesuada ut, consequat et diam. Nullam erat sem, rhoncus id ullamcorper vitae, rhoncus et arcu. In ultricies ultricies nulla, ut rutrum nisi iaculis at. Donec eu magna a metus ornare faucibus. Fusce aliquet faucibus ultricies. Morbi semper, est id tincidunt gravida, sem arcu adipiscing lacus, ac bibendum nulla leo eu purus. Quisque nec diam sed risus consectetur a ccumsan quis quis nibh. Vestibulum id purus lorem.</p>
    </div>
    <div class="letter__signature">
      <p class="person__name">John Doe</p>
      <p class="person__title">Co-Founder &amp; CEO</p>
    </div>
    <footer class="letter__footer">
      <p>Tolvane Arts Park 2850 Delmore Street Crest Hall, 2nd Floor Larkmoor Bay, CA 90412<span class="footer__divider"></span>P: 555-604-2187</p>
      <p>www.ambergatepicturesco.example</p>
    </footer>
  </section>

  <section class="sheet folder" aria-label="Presentation folder">
    <div class="folder__band"></div>
    <div class="brand-lockup">
      <span class="brand-dot"></span>
      <span class="brand-name">Amber Gate<br>Pictures</span>
    </div>
    <span class="folder__slot"></span>
  </section>

</body>
</html>
```